Venture Capital Investment Firm

We are looking to overhaul our existing website (substantially), with only using the same logos (which we can provide).
We are an investment firm that focuses on making loans to late stage technology companies. Our site should ultimately look like other venture capital firms, and look modern and fresh. We have an existing website www.norvellhub.com which this will be replacing, although we will be using a lot of the existing written content, and potentially the numbers of pages we will need, we are not wed to anything else. Please feel free to shoot any questions at any time and thank you in advance for your help!
Websites we like as examples:
https://www.tesmarkfund.com/
https://www.brindlewoodpartners.com/
Target Market(s)
Potential investors who will invest in our firm, as well as potentially companies that are looking to borrow money from us.
Coding
Coded - Design and coding required
Number of Pages Required
5+ page
Colors
Designer to choose colors to be used in the design.
Look and feel

```html
<!DOCTYPE html>
<html lang="en">
<head>
<meta charset="utf-8">
<title>Norvell IP — Structured Credit for Late Stage Technology</title>
<link href="https://fonts.googleapis.com/css2?family=Cinzel:wght@600;700&family=Open+Sans:wght@400;600&display=swap" rel="stylesheet">
<style>
:root{
  --navy:#0c0c47;
  --teal:#1e5c63;
  --teal-light:#3e8790;
  --grey-bg:#e7e6eb;
  --text:#6f6f78;
  --dark:#141414;
  --white:#fff;
}
*{margin:0;padding:0;box-sizing:border-box}
html,body{width:1200px;height:4501px;overflow:hidden}
body{font-family:"Open Sans",Arial,sans-serif;color:var(--text);background:var(--white);position:relative}
.abs{position:absolute}
.serif{font-family:"Cinzel",Georgia,serif;color:var(--navy);font-weight:700}
p{font-size:12px;line-height:19px}

/* header + hero */
.hero{position:absolute;left:0;top:0;width:1200px;height:638px;background:linear-gradient(180deg,#2a2622 0%,#3b342d 45%,#2a2621 100%)}
.topbar{position:absolute;left:0;top:0;width:1200px;height:28px;border-bottom:1px solid rgba(255,255,255,.35);color:#fff;font-size:11.5px}
.topbar span{position:absolute;top:7px}
.topbar u{text-decoration:underline}
.navbar{position:absolute;left:0;top:28px;width:1200px;height:72px;background:rgba(0,0,0,.45)}
.navbar a{position:absolute;top:31px;color:#fff;font-size:12px;text-decoration:none}
.brand{position:absolute;left:481px;top:0;width:239px;height:100px;background:var(--teal);clip-path:polygon(0 0,100% 0,100% 62%,50% 100%,0 62%);display:flex;align-items:flex-start;justify-content:center;padding-top:16px;gap:10px}
.brand i{width:22px;height:22px;border:2px solid #fff;border-radius:50%;margin-top:6px}
.brand b{font-family:"Cinzel",Georgia,serif;font-weight:600;color:#fff;font-size:30px}
.hero h1{position:absolute;left:0;top:212px;width:1200px;text-align:center;color:#fff;font-family:"Cinzel",Georgia,serif;font-size:45px;line-height:57px;font-weight:700}
.hero .lead{position:absolute;left:0;top:342px;width:1200px;text-align:center;color:#fff;font-size:14.5px;line-height:23px}
.hero .arrow{position:absolute;top:304px}

/* button */
.btn{position:absolute;height:48px;background:var(--teal-light);clip-path:polygon(14px 0,calc(100% - 14px) 0,100% 50%,calc(100% - 14px) 100%,14px 100%,0 50%)}
.btn span{position:absolute;inset:3px;background:var(--teal);clip-path:polygon(12px 0,calc(100% - 12px) 0,100% 50%,calc(100% - 12px) 100%,12px 100%,0 50%);display:flex;align-items:center;justify-content:center;color:#fff;font-family:"Cinzel",Georgia,serif;font-weight:700;font-size:15px;letter-spacing:.3px}

.sec-title{position:absolute;font-family:"Cinzel",Georgia,serif;color:var(--navy);font-weight:700;font-size:36px;text-align:center;width:1200px;left:0}
.orn{position:absolute}

/* photos */
.photo{position:absolute}

/* about */
.about h2{position:absolute;left:161px;top:706px;font-size:36px}
.stat{position:absolute;left:748px;top:1210px;width:244px;text-align:center}
.stat b{display:block;font-family:"Cinzel",Georgia,serif;color:var(--navy);font-size:36px}
.stat span{font-family:"Cinzel",Georgia,serif;color:var(--navy);font-weight:700;font-size:14px;line-height:21px}

.band-grey{position:absolute;left:0;width:1200px;background:var(--grey-bg)}

.item{position:absolute;width:340px}
.item h4{font-family:"Cinzel",Georgia,serif;color:var(--navy);font-weight:700;font-size:14px;margin-bottom:4px}
.item svg{position:absolute;left:-85px;top:0}

.benefits{position:absolute;left:858px;top:1729px;width:210px;height:240px;background:#03053f;color:#fff;padding:14px 16px}
.benefits h4{font-family:"Cinzel",Georgia,serif;font-size:17px;margin-bottom:8px}
.benefits p{font-size:11.5px;line-height:18px;color:#e6e6ef}
.benefits li{font-family:"Cinzel",Georgia,serif;font-weight:700;font-size:10.5px;margin:22px 0 0 22px}

.card{position:absolute;top:2877px;width:201px;height:224px;background:#fff;text-align:center;box-shadow:0 2px 8px rgba(0,0,0,.06)}
.card h4{font-family:"Cinzel",Georgia,serif;color:var(--navy);font-weight:700;font-size:14px;line-height:20px;margin-top:16px}
.card p{font-size:11.5px;line-height:19px;padding:0 12px}
.card svg{margin-top:26px}

.member{position:absolute;top:3434px;width:278px;height:249px;background:#fff;border:5px solid #f1f1f3;box-shadow:0 2px 8px rgba(0,0,0,.08);text-align:center}
.member .ph{position:absolute;left:11px;top:11px;width:246px;height:165px;background:radial-gradient(ellipse at 50% 70%,#555 0%,#1b1b1b 55%,#0a0a0a 100%)}
.member .role{position:absolute;left:11px;top:158px;width:246px;height:18px;background:var(--teal);color:#e7f1f2;font-size:9.5px;line-height:18px}
.member .name{position:absolute;left:0;top:186px;width:100%;font-family:"Cinzel",Georgia,serif;color:var(--navy);font-weight:700;font-size:14px;line-height:18px}
.member .title{position:absolute;left:0;top:207px;width:100%;display:block;font-size:11px;line-height:16px;color:var(--text)}

.news h5{font-family:"Cinzel",Georgia,serif;color:var(--navy);font-weight:700;font-size:11.5px;line-height:19px}
.news time{font-size:10.5px;color:var(--teal-light)}

footer{position:absolute;left:0;top:4268px;width:1200px;height:204px;background:var(--teal)}
.foot-brand{position:absolute;left:847px;top:0;width:353px;height:120px;background:#1a5259;clip-path:polygon(20px 0,100% 0,100% 100%,0 100%)}
.foot-name{position:absolute;left:918px;top:28px;color:#fff;font-family:"Cinzel",Georgia,serif;font-weight:600;font-size:30px;display:flex;align-items:center;gap:12px}
.foot-name i{width:30px;height:30px;border:2px solid #fff;border-radius:50%}
.foot-sub{position:absolute;left:1012px;top:68px;color:#fff;font-size:8.5px;font-weight:600;letter-spacing:.4px}
.contact{position:absolute;top:112px;color:#fff;font-size:12px;display:flex;align-items:center;gap:14px}
.social{position:absolute;top:112px;width:30px;height:30px;border:1.5px solid #fff;border-radius:50%}
.copy{position:absolute;left:0;top:4472px;width:1200px;height:29px;background:var(--dark);color:#ddd;font-size:11.5px;text-align:center;line-height:29px}
</style>
</head>
<body>

<!-- HERO -->
<section class="hero" role="img" aria-label="Dimmed office photo of people planning on a sticky-note wall">
  <div class="topbar">
    <span style="left:162px"><u>Call Us On</u>: +1-555-010-0199</span>
    <span style="left:836px"><u>Mail Us On</u>: inquiries@norvellhub.com</span>
  </div>
  <nav class="navbar">
    <a style="left:162px">Home</a><a style="left:227px">About Us</a><a style="left:310px">Strategy</a>
    <a style="left:770px">Investors</a><a style="left:852px">Team</a><a style="left:914px">News</a><a style="left:976px">Contact Us</a>
  </nav>
  <div class="brand"><i></i><b>Norvell</b></div>
  <h1>We Focuses On Making<br>Loans To Late Stage Technology</h1>
  <div class="lead">We Are A Global Structured Credit Investment Firm Focused On The<br>Healthcare And Technology Industries</div>
  <div class="btn" style="left:485px;top:420px;width:230px"><span>Investors Login</span></div>
  <svg class="arrow" style="left:62px" width="26" height="26" viewBox="0 0 26 26" fill="none" stroke="#fff" stroke-width="3"><path d="M3 3v20M22 13H8M13 7l-6 6 6 6"/></svg>
  <svg class="arrow" style="left:1112px" width="26" height="26" viewBox="0 0 26 26" fill="none" stroke="#fff" stroke-width="3"><path d="M23 3v20M4 13h14M13 7l6 6-6 6"/></svg>
</section>

<!-- ABOUT -->
<section class="about">
  <h2 class="serif">About Us</h2>
  <svg class="orn" style="left:161px;top:750px" width="190" height="14"><line x1="0" y1="7" x2="190" y2="7" stroke="#0c0c47" stroke-width="1.5"/><circle cx="90" cy="7" r="5" fill="#fff" stroke="#0c0c47" stroke-width="1.5"/><circle cx="100" cy="7" r="5" fill="#fff" stroke="#0c0c47" stroke-width="1.5"/></svg>
  <p class="abs" style="left:161px;top:780px;width:430px">Norvell IP is a private investment firm unique in its dual focus on life science and technology credit opportunities. Our ambidextrous approach to investing reflects a broad recognition and appreciation for the critical role intellectual property plays in the successful commercialization of products. We apply our extensive industry expertise to assess the revenue visibility created by these assets and offer a range of creative financing solutions.</p>
  <div class="btn" style="left:161px;top:935px;width:158px;height:46px"><span style="font-size:14px">Read More</span></div>
  <div class="photo" role="img" aria-label="Photo of a person counting banknotes at a desk with a notebook, calculator and phone" style="left:641px;top:676px;width:376px;height:508px;background:linear-gradient(160deg,#2c3a48 0%,#1b2530 55%,#0f151b 100%)"></div>
  <div class="photo" role="img" aria-label="Photo of a calculator and pen on printed financial figures" style="left:161px;top:1043px;width:562px;height:299px;background:linear-gradient(120deg,#5a5a5c 0%,#9c9c9e 45%,#cfcfd0 100%)"></div>
  <div class="stat"><b>40</b><span>Years of<br>Collective Experience</span></div>
</section>

<!-- STRATEGY -->
<section class="band-grey" style="top:1436px;height:674px"></section>
<div class="sec-title" style="top:1497px">Our Strategy</div>
<svg class="orn" style="left:505px;top:1541px" width="190" height="14"><line x1="0" y1="7" x2="190" y2="7" stroke="#0c0c47" stroke-width="1.5"/><circle cx="90" cy="7" r="5" fill="#e7e6eb" stroke="#0c0c47" stroke-width="1.5"/><circle cx="100" cy="7" r="5" fill="#e7e6eb" stroke="#0c0c47" stroke-width="1.5"/></svg>
<h3 class="abs serif" style="left:161px;top:1615px;font-size:24px">Life Sciences</h3>
<p class="abs" style="left:161px;top:1648px;width:420px">Our focus spans the life science and technology industries, two sectors where intellectual property (IP) is an integral driver of asset and enterprise value.</p>

<div class="item" style="left:245px;top:1738px">
  <svg width="64" height="64" viewBox="0 0 64 64" fill="none" stroke="#1e5c63" stroke-width="2"><rect x="6" y="8" width="24" height="8"/><rect x="4" y="16" width="28" height="40" rx="3"/><rect x="10" y="28" width="16" height="14"/><circle cx="44" cy="42" r="12"/><path d="M36 50l16-16"/></svg>
  <h4>Biopharma</h4>
  <p>Lorem Ipsum is simply dummy text of the printing and typesetting industry. Lorem Ipsum has been the industry's standard dummy text.</p>
</div>
<div class="item" style="left:245px;top:1851px">
  <svg width="64" height="64" viewBox="0 0 64 64" fill="none" stroke="#1e5c63" stroke-width="2"><rect x="18" y="6" width="28" height="50" rx="2"/><rect x="23" y="12" width="18" height="14"/><path d="M46 20h8v20h-8M10 30h8M14 26v8M24 56v4h16v-4"/></svg>
  <h4>Devices</h4>
  <p>Lorem Ipsum is simply dummy text of the printing and typesetting industry. Lorem Ipsum has been the industry's standard dummy text.</p>
</div>
<div class="item" style="left:245px;top:1964px">
  <svg width="64" height="64" viewBox="0 0 64 64" fill="none" stroke="#1e5c63" stroke-width="2"><path d="M20 10v18L8 54h28L26 28V10M16 10h14"/><rect x="42" y="24" width="10" height="32"/><path d="M12 44h20M6 6l2 2M40 10l2-2"/></svg>
  <h4>Tools &amp; Diagnostics</h4>
  <p>Lorem Ipsum is simply dummy text of the printing and typesetting industry. Lorem Ipsum has been the industry's standard dummy text.</p>
</div>
<div class="photo" role="img" aria-label="Photo of a bearded man in a white shirt reading his phone at a table" style="left:611px;top:1616px;width:338px;height:428px;background:linear-gradient(110deg,#3a3430 0%,#8b7d6e 45%,#d9d2c8 100%)"></div>
<div class="benefits">
  <h4>Key Benefits</h4>
  <p>We seek to fill a void in the capital markets where too often complexity.</p>
  <ul>
    <li>Structured Credit</li>
    <li>Milestones &amp; Royalties</li>
    <li>Legacy Assets</li>
  </ul>
</div>

<!-- TECHNOLOGY -->
<div class="photo" role="img" aria-label="Photo of a smiling team gathered around a laptop in an office" style="left:101px;top:2198px;width:563px;height:419px;background:linear-gradient(135deg,#4a4643 0%,#8d8680 50%,#cbc6c0 100%)"></div>
<h3 class="abs serif" style="left:695px;top:2196px;font-size:24px">Technology</h3>
<p class="abs" style="left:695px;top:2228px;width:330px">We uniquely offer sizeable and flexible structured credit financing solutions to innovative technology companies, with a focus on enterprise software.</p>
<div class="item" style="left:785px;top:2325px;width:260px">
  <svg style="left:-77px" width="58" height="58" viewBox="0 0 58 58" fill="none" stroke="#1e5c63" stroke-width="2"><rect x="4" y="4" width="46" height="50" rx="2"/><circle cx="26" cy="26" r="12"/><path d="M35 35l12 12M8 46h20"/></svg>
  <h4>Software &amp; Services</h4>
  <p>Lorem Ipsum is simply dummy text of the printing and typesetting industry.</p>
</div>
<div class="item" style="left:785px;top:2438px;width:260px">
  <svg style="left:-77px" width="58" height="58" viewBox="0 0 58 58" fill="none" stroke="#1e5c63" stroke-width="2"><rect x="6" y="6" width="46" height="46" rx="2"/><rect x="14" y="14" width="26" height="26"/><path d="M20 22h14M20 28h14M20 34h10M6 46h46"/></svg>
  <h4>Hardware</h4>
  <p>Lorem Ipsum is simply dummy text of the printing and typesetting industry.</p>
</div>
<div class="item" style="left:785px;top:2550px;width:260px">
  <svg style="left:-77px" width="58" height="58" viewBox="0 0 58 58" fill="none" stroke="#1e5c63" stroke-width="2"><rect x="4" y="6" width="50" height="46" rx="3"/><path d="M4 16h50M12 24h34v8H12zM12 38h14v8H12zM32 38h14v8H32z"/></svg>
  <h4>Systems</h4>
  <p>Lorem Ipsum is simply dummy text of the printing and typesetting industry.</p>
</div>

<!-- TRANSACTION TYPE -->
<section class="band-grey" style="top:2699px;height:577px"></section>
<div class="sec-title" style="top:2759px;font-size:28px">Transaction Type</div>
<p class="abs" style="left:300px;top:2797px;width:600px;text-align:center">Norvell IP's proven strategy focuses on identifying opportunities where demonstrated commercial success has established underlying asset or enterprise value prior to our investment.</p>
<div class="card" style="left:274px">
  <svg width="72" height="56" viewBox="0 0 72 56" fill="none" stroke="#1e5c63" stroke-width="2.5"><rect x="4" y="4" width="50" height="34" rx="3"/><path d="M4 14h50"/><rect x="18" y="20" width="50" height="32" rx="3" fill="#fff"/><path d="M26 40h16M52 40h8"/></svg>
  <h4>Structured<br>Credit</h4>
  <p>Lorem Ipsum is simply dummy text of the printing and type setting industry.</p>
</div>
<div class="card" style="left:500px">
  <svg width="64" height="56" viewBox="0 0 64 56" fill="none" stroke="#1e5c63" stroke-width="2.5"><circle cx="32" cy="8" r="5"/><path d="M24 24a8 8 0 0116 0M10 26h44M14 26v10h36V26M8 40h48M12 40v12M52 40v12M24 44h16"/></svg>
  <h4>Milestones &amp;<br>Royalties</h4>
  <p>Lorem Ipsum is simply dummy text of the printing and type setting industry.</p>
</div>
<div class="card" style="left:725px">
  <svg width="64" height="60" viewBox="0 0 64 60" fill="none" stroke="#1e5c63" stroke-width="2.5"><path d="M4 28a28 24 0 0156 0M32 4v24M18 28c0-12 6-24 14-24s14 12 14 24"/><circle cx="22" cy="42" r="10"/><circle cx="42" cy="42" r="10"/><path d="M22 36v12M42 36v12"/></svg>
  <h4>Legacy<br>Assets</h4>
  <p>Lorem Ipsum is simply dummy text of the printing and type setting industry.</p>
</div>
<div class="btn" style="left:506px;top:3161px;width:188px;height:46px"><span style="font-size:14px">Explore More</span></div>

<!-- TEAM -->
<div class="sec-title" style="top:3339px">Our Team</div>
<svg class="orn" style="left:505px;top:3383px" width="190" height="14"><line x1="0" y1="7" x2="190" y2="7" stroke="#0c0c47" stroke-width="1.5"/><circle cx="90" cy="7" r="5" fill="#fff" stroke="#0c0c47" stroke-width="1.5"/><circle cx="100" cy="7" r="5" fill="#fff" stroke="#0c0c47" stroke-width="1.5"/></svg>
<div class="member" style="left:161px"><div class="ph" role="img" aria-label="Black and white portrait of a managing partner"></div><div class="role">Life Sciences, Technology</div><div class="name">Elias Marlowe</div><div class="title">Managing Partner</div></div>
<div class="member" style="left:461px"><div class="ph" role="img" aria-label="Black and white portrait of a managing partner"></div><div class="role">Technology</div><div class="name">Tarek Vandermeer</div><div class="title">Managing Partner</div></div>
<div class="member" style="left:762px"><div class="ph" role="img" aria-label="Black and white portrait of the chief operating officer"></div><div class="role">Chief Operating Officer</div><div class="name">Owen Halstead</div><div class="title">Partner</div></div>
<div class="btn" style="left:521px;top:3735px;width:158px;height:46px"><span style="font-size:14px">Read More</span></div>

<!-- NEWS -->
<div class="sec-title" style="top:3842px">Latest News</div>
<svg class="orn" style="left:505px;top:3885px" width="190" height="14"><line x1="0" y1="7" x2="190" y2="7" stroke="#0c0c47" stroke-width="1.5"/><circle cx="90" cy="7" r="5" fill="#fff" stroke="#0c0c47" stroke-width="1.5"/><circle cx="100" cy="7" r="5" fill="#fff" stroke="#0c0c47" stroke-width="1.5"/></svg>
<div class="news">
  <div class="photo" role="img" aria-label="Photo of an office with wood panelling and people at a meeting table" style="left:161px;top:3934px;width:428px;height:224px;background:linear-gradient(90deg,#3c1e16 0%,#6b3d2c 30%,#c9c3bb 60%,#5a3426 100%)"></div>
  <div class="abs" style="left:161px;top:4170px;width:430px"><h5>Completion of $36,250,000 structured credit investment in Kestrel Semiconductor</h5><time>25 December 2014</time></div>
  <div class="photo" role="img" aria-label="Photo of a business meeting" style="left:610px;top:3934px;width:113px;height:75px;background:linear-gradient(135deg,#6d6d70,#c6c6c8)"></div>
  <div class="abs" style="left:732px;top:3936px;width:300px"><h5>Norvell IP completes structured debt investment in BrightLoom</h5><time>26 April 2018</time></div>
  <div class="photo" role="img" aria-label="Photo of hands working on a laptop" style="left:610px;top:4032px;width:113px;height:73px;background:linear-gradient(135deg,#3a3f55,#a5a8b8)"></div>
  <div class="abs" style="left:735px;top:4034px;width:300px"><h5>Kestrel Semiconductor acquired by Ridgewave for $55,000,000</h5><time>03 April 2018</time></div>
  <div class="photo" role="img" aria-label="Photo of a calculator on financial papers" style="left:610px;top:4130px;width:113px;height:73px;background:linear-gradient(135deg,#55575a,#d2d2d2)"></div>
  <div class="abs" style="left:732px;top:4132px;width:310px"><h5>Norvell IP completes $15,000,000 structured credit investment in Tempora Labs</h5><time>06 september 2014</time></div>
</div>

<!-- FOOTER -->
<footer>
  <div class="foot-brand"></div>
  <div class="foot-name"><i></i>Norvell IP</div>
  <div class="foot-sub">INVESTMENT PARTNERS, LLC</div>
  <div class="contact" style="left:161px">
    <svg width="36" height="36" viewBox="0 0 36 36" fill="none" stroke="#fff" stroke-width="1.8"><circle cx="18" cy="18" r="16"/><path d="M12 11l4 0 2 5-2 2a10 10 0 005 5l2-2 5 2v4c-9 1-17-7-16-16z"/></svg>
    <span style="font-weight:600">+1-555-010-0199</span>
  </div>
  <div class="contact" style="left:384px">
    <svg width="36" height="36" viewBox="0 0 36 36" fill="none" stroke="#fff" stroke-width="1.8"><circle cx="18" cy="18" r="16"/><rect x="10" y="12" width="16" height="12"/><path d="M10 12l8 7 8-7"/></svg>
    <span>inquiries@norvellhub.com</span>
  </div>
  <div class="contact" style="left:650px">
    <svg width="36" height="36" viewBox="0 0 36 36" fill="none" stroke="#fff" stroke-width="1.8"><circle cx="18" cy="18" r="16"/><path d="M18 28s-7-7-7-12a7 7 0 0114 0c0 5-7 12-7 12z"/><circle cx="18" cy="16" r="2.5"/></svg>
    <span style="font-size:11.5px;line-height:18px">220 Larkspur Avenue #310<br>Oakland, CA  94607</span>
  </div>
  <span class="social" style="left:963px" aria-label="Social profile"></span>
  <span class="social" style="left:1006px" aria-label="Social profile"></span>
  <span class="social" style="left:1049px" aria-label="Social profile"></span>
  <span class="social" style="left:1092px" aria-label="Social profile"></span>
</footer>
<div class="copy">Copyrights © 2019 Norvell IP. All Rights Reserved, Terms &amp; Conditions  |  Privacy Policy.</div>

</body>
</html>
```